Business Card Design Project

This is the first time we use our new logo. We need a business card that we can use both on our institutional corporate relationships and also that works for our staff that deals with consumers directly.

VELUNDA is a new company dedicated to empower consumers and to provide them with the best choices for specialized health care using the latest telemedicine technology (medicine at a distance via videoconference).

We want to print this cards in high quality materials and process. We will like designs that allow us to use UV spot varnish and other techniques that will differentiate us.

We are including Two different versions of Color logos. In addition we are including white over black background logos. Those can be used replacing the black for a color.

Please note this is the first time we will be creating any corporate materials with our new logo and colors.

Target Market(s)

34+ consumers of medium high and high socioeconomic levels.

Industry/Entity Type

Health

Requirements
Must have
• Our logo on its original colors
Should not have
• Any other graphical element or design that is not our logo

```html
<!DOCTYPE html>
<html lang="en">
<head>
<meta charset="utf-8">
<title>VELUNDA Business Card</title>
<link href="https://fonts.googleapis.com/css2?family=Poppins:wght@600&family=Arimo:wght@400;700&display=swap" rel="stylesheet">
<style>
  :root {
    --bg: #e9e6e1;
    --card: #ffffff;
    --navy: #1d5a84;
    --teal: #13a79a;
    --sky: #5bb3de;
    --ink: #2b2b2b;
    --muted: #4a4a4a;
  }
  html, body {
    margin: 0;
    padding: 0;
    width: 1200px;
    height: 1057px;
    overflow: hidden;
    background: var(--bg);
  }
  .sheet {
    position: relative;
    width: 1200px;
    height: 1057px;
  }
  .card {
    position: absolute;
    left: 180px;
    width: 840px;
    height: 480px;
    background: var(--card);
    box-shadow: 0 6px 18px rgba(0,0,0,0.18);
    overflow: hidden;
  }
  .card--front { top: 36px; }
  .card--back { top: 550px; }

  .brand {
    position: absolute;
    display: flex;
    align-items: center;
  }
  .brand__dot {
    border-radius: 50%;
    background: var(--teal);
    flex: none;
  }
  .brand__name {
    font-family: "Poppins", sans-serif;
    font-weight: 600;
    color: var(--navy);
    letter-spacing: 0.08em;
    line-height: 1;
  }

  .card--front .brand { left: 70px; top: 70px; }
  .card--front .brand__dot { width: 62px; height: 62px; margin-right: 26px; }
  .card--front .brand__name { font-size: 60px; }

  .holder {
    position: absolute;
    left: 70px;
    top: 210px;
    margin: 0;
    font-family: "Arimo", sans-serif;
  }
  .holder__name {
    font-weight: 700;
    font-size: 30px;
    color: var(--navy);
  }
  .holder__title {
    font-weight: 400;
    font-size: 24px;
    color: var(--teal);
  }

  .contacts {
    position: absolute;
    left: 70px;
    top: 262px;
    margin: 0;
    padding: 0;
    list-style: none;
    font-family: "Arimo", sans-serif;
    font-size: 21px;
    color: var(--ink);
  }
  .contacts li {
    display: flex;
    align-items: center;
    height: 30px;
  }
  .contacts svg {
    width: 18px;
    height: 18px;
    margin-right: 12px;
    flex: none;
  }
  .address {
    position: absolute;
    left: 70px;
    top: 400px;
    margin: 0;
    font-family: "Arimo", sans-serif;
    font-size: 21px;
    color: var(--ink);
  }

  .card--back .brand {
    left: 0;
    right: 0;
    top: 150px;
    justify-content: center;
  }
  .card--back .brand__dot { width: 90px; height: 90px; margin-right: 34px; }
  .card--back .brand__name { font-size: 88px; }
  .web {
    position: absolute;
    left: 0;
    right: 0;
    top: 330px;
    margin: 0;
    text-align: center;
    font-family: "Arimo", sans-serif;
    font-size: 26px;
    letter-spacing: 0.32em;
    color: var(--ink);
  }
  .web__domain { color: var(--navy); font-weight: 700; }
</style>
</head>
<body>
<main class="sheet">

  <section class="card card--front" aria-label="Card front">
    <div class="brand">
      <span class="brand__dot"></span>
      <span class="brand__name">VELUNDA</span>
    </div>

    <p class="holder">
      <span class="holder__name">Your Name,</span>
      <span class="holder__title">Title</span>
    </p>

    <ul class="contacts">
      <li>
        <svg viewBox="0 0 20 20" aria-hidden="true"><circle cx="10" cy="10" r="9" fill="none" stroke="var(--navy)" stroke-width="1.6"/><path d="M7 5.5c-1 .8-1.3 2-.7 3.6.8 2.2 2.4 4 4.4 5 1.3.6 2.4.4 3.1-.5l-1.6-1.6-1.3.8c-1-.5-2-1.6-2.5-2.7l.8-1.2z" fill="var(--navy)"/></svg>
        012-555-0148
      </li>
      <li>
        <svg viewBox="0 0 20 20" aria-hidden="true"><circle cx="10" cy="10" r="9" fill="none" stroke="var(--navy)" stroke-width="1.6"/><path d="M7 5.5c-1 .8-1.3 2-.7 3.6.8 2.2 2.4 4 4.4 5 1.3.6 2.4.4 3.1-.5l-1.6-1.6-1.3.8c-1-.5-2-1.6-2.5-2.7l.8-1.2z" fill="var(--navy)"/></svg>
        012-555-0148
      </li>
      <li>
        <svg viewBox="0 0 20 20" aria-hidden="true"><rect x="2" y="5" width="16" height="11" rx="1" fill="var(--navy)"/><path d="M2.5 5.5 10 11l7.5-5.5" fill="none" stroke="#fff" stroke-width="1.4"/></svg>
        name@velunda.com
      </li>
      <li>
        <svg viewBox="0 0 20 20" aria-hidden="true"><g fill="none" stroke="var(--navy)" stroke-width="1.4"><circle cx="10" cy="10" r="8"/><ellipse cx="10" cy="10" rx="3.5" ry="8"/><path d="M2 10h16M3.5 6h13M3.5 14h13"/></g></svg>
        www.velunda.com
      </li>
    </ul>

    <p class="address">Street Name, City Name, State, City Zip Code</p>
  </section>

  <section class="card card--back" aria-label="Card back">
    <div class="brand">
      <span class="brand__dot"></span>
      <span class="brand__name">VELUNDA</span>
    </div>
    <p class="web">www.<span class="web__domain">velunda</span>.com</p>
  </section>

</main>
</body>
</html>
```